Professional Package for CPA Firm

We would like a stationery design for our new CPA Firm based in Atlanta, GA called 'Vale 8'. We work with investors to help grow investments, tax free. We would like the design to have a professional/minimal look with a 'wow' factor. We need 9.5″ x 4.125″, 9x12, and 10x13 mailing envelopes, business cards, and a letterhead. We have a logo that is already complete. For the letterhead, we would like to have space to put credentials at the bottom of the page

Industry/Entity Type

CPA, Accounting

```html
<!DOCTYPE html>
<html lang="en">
<head>
<meta charset="utf-8">
<title>Vale 8 — Business Card</title>
<link rel="stylesheet" href="https://fonts.googleapis.com/css2?family=Lato:wght@400;700&display=swap">
<style>
  :root {
    --backdrop: #9b9b9b;
    --coral: #ff454b;
    --teal: #1aa3b5;
    --navy: #0b2a40;
    --card-dark: #042b3f;
    --brand-blue: #1591c8;
    --white: #ffffff;
  }
  html, body {
    margin: 0;
    padding: 0;
    width: 1200px;
    height: 1200px;
    overflow: hidden;
    background: var(--backdrop);
    font-family: "Lato", Arial, sans-serif;
  }
  .canvas {
    position: relative;
    width: 1200px;
    height: 1200px;
  }
  .card {
    position: absolute;
    left: 261px;
    width: 686px;
    height: 392px;
    display: block;
  }
  .card--front { top: 165px; }
  .card--back { top: 653px; }
  .card text { font-family: "Lato", Arial, sans-serif; }
  .holder-name { font-size: 26px; font-weight: 700; fill: var(--white); }
  .holder-role, .holder-line { font-size: 18px; font-weight: 400; fill: var(--white); }
  .brand-name { font-weight: 700; letter-spacing: 4px; }
  .brand-tagline { font-weight: 400; letter-spacing: 2px; }
</style>
</head>
<body>
<main class="canvas">

  <svg class="card card--front" viewBox="0 0 800 457" preserveAspectRatio="none" aria-label="Business card front">
    <rect class="card-base" width="800" height="457" fill="var(--white)"/>
    <polygon class="coral-panel" points="0,0 213,0 460,457 0,457" fill="var(--coral)"/>
    <polygon class="accent-stripe accent-stripe--teal" points="253,68 266,68 481,457 468,457" fill="var(--teal)"/>
    <polygon class="accent-stripe accent-stripe--navy" points="295,109 311,109 497,457 481,457" fill="var(--navy)"/>

    <text class="holder-name" x="50" y="227">DANIEL REYES</text>
    <text class="holder-role" x="50" y="250">President</text>
    <text class="holder-line" x="52" y="284">412 Birchwood Court</text>
    <text class="holder-line" x="52" y="306">Marietta, Georgia 30060</text>

    <g class="contact-icons" fill="var(--white)">
      <path class="icon-phone" d="M53,329 c1,-2 3,-3 4,-1 l2,3 c1,1 0,2 -1,3 c1,2 3,4 5,5 c1,-1 2,-2 3,-1 l3,2 c2,1 1,3 -1,4 c-6,2 -17,-9 -15,-15 z"/>
      <rect class="icon-mobile" x="54" y="348" width="10" height="15" rx="1.5" fill="none" stroke="var(--white)" stroke-width="2"/>
      <path class="icon-mail" d="M52,374 h13 v9 h-13 z M52,374 l6.5,5 l6.5,-5" fill="var(--white)" stroke="var(--coral)" stroke-width="1"/>
      <circle class="icon-globe" cx="58.5" cy="403" r="6.5"/>
      <path d="M55,399 c2,1 3,3 2,5 c-1,2 0,4 2,5 M61,398 c-1,2 1,3 3,3" fill="none" stroke="var(--coral)" stroke-width="1.3"/>
    </g>
    <text class="holder-line" x="76" y="340">555-214-7730</text>
    <text class="holder-line" x="76" y="363">555-386-4192</text>
    <text class="holder-line" x="76" y="385">info@vale8.com</text>
    <text class="holder-line" x="76" y="408">www.vale8.com</text>

    <text class="brand-name" x="605" y="250" text-anchor="middle" font-size="62" fill="var(--navy)">VALE 8</text>
    <text class="brand-tagline" x="605" y="276" text-anchor="middle" font-size="17" fill="var(--navy)">CPAs and Tax Advisors</text>
  </svg>

  <svg class="card card--back" viewBox="0 0 800 457" preserveAspectRatio="none" aria-label="Business card back">
    <rect class="card-base" width="800" height="457" fill="var(--card-dark)"/>
    <text class="brand-name" x="400" y="328" text-anchor="middle" font-size="74" fill="var(--brand-blue)">VALE 8</text>
    <text class="brand-tagline" x="400" y="360" text-anchor="middle" font-size="20" fill="var(--brand-blue)">CPAs and Tax Advisors</text>
  </svg>

</main>
</body>
</html>
```